BrimFalcon Business Cards

We have a defined brand. Please visit our website to get a feel for the product and the color pallets. www.brimfalcon-example.com

We need an updated, world class business card design. (See the attached existing card design). Please utilize BOTH sides of the card as shown and be creative with the layout. I do want the horse head icon to be positioned as it is with the existing card.

The remainder of the layout can be customized and I also want it vertically oriented.

Attached are the logo files and please use the colors as follows:
Green - #A5CE39
Tan - #CDBD99
Black

Feel free to play with the colors.

```html
<!DOCTYPE html>
<html lang="en">
<head>
<meta charset="utf-8">
<title>BrimFalcon Business Card</title>
<link href="https://fonts.googleapis.com/css2?family=Ubuntu:wght@400;500;700&display=swap" rel="stylesheet">
<style>
  :root {
    --green: #96c131;
    --black: #141414;
    --white: #f4f4f4;
    --ink: #1a1a1a;
    --stage: #d9d9d6;
    --pattern-light: #f2f2f2;
    --pattern-dark: #dcdcdc;
  }
  * { box-sizing: border-box; margin: 0; padding: 0; }
  html, body { width: 1200px; height: 985px; overflow: hidden; }
  body {
    background: var(--stage);
    font-family: "Ubuntu", sans-serif;
    position: relative;
  }
  .card {
    position: absolute;
    top: 192px;
    width: 360px;
    height: 600px;
    border-radius: 14px;
    overflow: hidden;
    box-shadow: 0 6px 18px rgba(0,0,0,0.18);
  }
  .card--front { left: 205px; background: var(--white); }
  .card--back { left: 635px; }

  /* front */
  .brand-area {
    height: 170px;
    display: flex;
    align-items: center;
    justify-content: center;
    gap: 12px;
  }
  .brand-area__dot {
    width: 22px; height: 22px; border-radius: 50%;
    background: var(--ink);
  }
  .brand-area__name {
    font-weight: 700;
    font-size: 38px;
    color: var(--ink);
  }
  .name-band {
    height: 70px;
    background: var(--black);
    text-align: center;
    color: var(--green);
    padding-top: 10px;
  }
  .name-band__name { font-weight: 700; font-size: 22px; letter-spacing: 0.5px; line-height: 1.2; }
  .name-band__title { font-size: 17px; margin-top: 1px; letter-spacing: 0.5px; line-height: 1.2; }

  .contact-row { display: flex; height: 90px; }
  .contact-row__icon {
    width: 96px;
    flex-shrink: 0;
    display: flex; align-items: center; justify-content: center;
  }
  .contact-row__text {
    flex: 1;
    min-width: 0;
    display: flex; align-items: center;
    padding-left: 22px;
    font-size: 17px;
    letter-spacing: 0.6px;
    white-space: nowrap;
  }
  .contact-row--dark .contact-row__icon { background: var(--green); }
  .contact-row--dark .contact-row__text { background: var(--black); color: var(--green); }
  .contact-row--light .contact-row__icon { background: var(--black); }
  .contact-row--light .contact-row__text { background: var(--green); color: var(--ink); }
  .contact-row__text--small { font-size: 14px; padding-left: 14px; letter-spacing: 0.2px; }

  .address {
    height: 90px;
    display: flex; flex-direction: column; align-items: center; justify-content: center;
    font-size: 20px; font-weight: 500; color: var(--ink);
    letter-spacing: 0.6px; line-height: 1.2;
  }

  /* back */
  .back-pattern {
    position: absolute; inset: 0;
    background: linear-gradient(135deg, var(--pattern-light), var(--pattern-dark));
  }
  .back-wordmark {
    position: absolute;
    left: 50%; top: 50%;
    transform: translate(-50%, -50%) rotate(90deg);
    display: flex; align-items: center; gap: 14px;
    white-space: nowrap;
  }
  .back-wordmark__dot {
    width: 34px; height: 34px; border-radius: 50%;
    background: var(--ink);
  }
  .back-wordmark__name {
    font-weight: 700;
    font-size: 52px;
    color: var(--ink);
  }
</style>
</head>
<body>

<section class="card card--front">
  <div class="brand-area">
    <span class="brand-area__dot"></span>
    <span class="brand-area__name">BrimFalcon</span>
  </div>

  <div class="name-band">
    <div class="name-band__name">Dana Kessler</div>
    <div class="name-band__title">President &amp; CEO</div>
  </div>

  <div class="contact-row contact-row--dark">
    <div class="contact-row__icon">
      <svg width="48" height="40" viewBox="0 0 48 40" aria-hidden="true">
        <path d="M4 12 Q24 0 44 12 L44 16 L36 16 L34 11 Q24 8 14 11 L12 16 L4 16 Z" fill="#141414"/>
        <path d="M12 18 L36 18 L42 36 L6 36 Z" fill="#141414"/>
        <g fill="#96c131">
          <rect x="17" y="22" width="3" height="3"/><rect x="22.5" y="22" width="3" height="3"/><rect x="28" y="22" width="3" height="3"/>
          <rect x="17" y="27" width="3" height="3"/><rect x="22.5" y="27" width="3" height="3"/><rect x="28" y="27" width="3" height="3"/>
        </g>
      </svg>
    </div>
    <div class="contact-row__text">555.014.7391</div>
  </div>

  <div class="contact-row contact-row--light">
    <div class="contact-row__icon">
      <svg width="52" height="36" viewBox="0 0 52 36" aria-hidden="true">
        <rect x="2" y="2" width="48" height="32" fill="none" stroke="#96c131" stroke-width="3"/>
        <path d="M2 2 L26 20 L50 2 M2 34 L20 16 M50 34 L32 16" fill="none" stroke="#96c131" stroke-width="3"/>
      </svg>
    </div>
    <div class="contact-row__text">Dana@BrimFalcon.com</div>
  </div>

  <div class="contact-row contact-row--dark">
    <div class="contact-row__icon">
      <svg width="46" height="46" viewBox="0 0 46 46" aria-hidden="true">
        <circle cx="23" cy="23" r="21" fill="#141414"/>
        <g fill="none" stroke="#96c131" stroke-width="1.6">
          <ellipse cx="23" cy="23" rx="9" ry="21"/>
          <line x1="2" y1="23" x2="44" y2="23"/>
          <line x1="5" y1="13" x2="41" y2="13"/>
          <line x1="5" y1="33" x2="41" y2="33"/>
          <line x1="23" y1="2" x2="23" y2="44"/>
        </g>
      </svg>
    </div>
    <div class="contact-row__text contact-row__text--small">www.brimfalconlabs-example.com</div>
  </div>

  <div class="address">
    <span>Northvale, Lakeshire</span>
    <span>canada</span>
  </div>
</section>

<section class="card card--back">
  <div class="back-pattern" role="img" aria-label="Faint repeating brand emblem pattern in light grey"></div>
  <div class="back-wordmark">
    <span class="back-wordmark__dot"></span>
    <span class="back-wordmark__name">BrimFalcon Labs</span>
  </div>
</section>

</body>
</html>
```